Very new and innovative Web design for Property managers of Vacation rentals

We are looking for a new website design for travel agencies and property managers specialised on vacation rentals business, holiday villas and apartments.

The end users of this website are travellers who are looking for a vacation home for their next holiday: this is the reason why the website must be easy to use, attractive, professional, possibly elegant and focused on get new reservations.

This is a draft of our current website: https://intro3.kelumsito.com/
Please consider that we would like to have proposals with a totally different and innovative layout, surprise us!

These are the pages of the website:
• Homepage: feel free to redesign all the homepage as you wish, surprise us with something very new! Please consider that Property manager/Travel agencies usually want to have the opportunity to put in evidence groups of houses with specific characteristics (eg. villas with private swimming pool, apartment in big/small towns, villas with air co, etc…), destinations and tourist areas, and sometimes experiences or activities (please consider that the website layout must be suitable even if some of the previous sections are not used).
• Search page: we’d like to organise the results of the search page in three different ways:
o Grid
o Map
o List
• Property page: to illustrate the characteristics, descriptions, images, …. of the property. It is very important to put in evidence images of the property and to maintain the booking form (and the other call to action bottom – eg. whatsapp) always visible
• Custom pages: static pages composed usually by text, images and call to actions
• Contact us (general form)
• Info request (specific of a property form)
• Booking process
• Blog, organised in four pages:
o Home Page – introduction to the blog
o List of articles
o Single article
o Site Map (presentation of categories and sub-categories)

If possible, we’d prefer to receive the material in Adobe XD or similar so that we can obtain the three versions:
- smartphone
- tablet
- desktop

The website will be then developed in Bootstrap: as a result we’ll need the icons in SVG format (or the library used)

In attachment you can find the map of the website pages

```html
<!DOCTYPE html>
<html lang="en">
<head>
<meta charset="utf-8">
<title>VillaHaven – Vacation Rental Website Pages</title>
<link rel="stylesheet" href="https://fonts.googleapis.com/css2?family=PT+Sans+Narrow:wght@400;700&family=Poppins:wght@400;500;600&display=swap">
<style>
:root{
  --board:#f4f6f8;
  --page:#ffffff;
  --ink:#2c3838;
  --text:#333b3b;
  --muted:#8a9292;
  --line:#d9dede;
  --green:#1fcb8b;
  --green-dark:#15a872;
  --dark:#232526;
  --dark-2:#1b1c1d;
  --navy:#12203a;
}
*{box-sizing:border-box;margin:0;padding:0}
html,body{width:1200px;height:2352px;overflow:hidden}
body{background:var(--board);font-family:"Poppins",sans-serif;color:var(--text);position:relative}
ul{list-style:none}
.board-title{position:absolute;width:378px;text-align:center;font-family:"PT Sans Narrow",sans-serif;font-weight:700;font-size:35px;letter-spacing:1px;color:var(--ink);line-height:1}
.page{position:absolute;width:378px;background:var(--page);overflow:hidden;box-shadow:0 2px 10px rgba(0,0,0,.08)}
.abs{position:absolute}
.ph{position:absolute}
.hdr{position:absolute;left:0;top:0;width:378px;height:76px}
.logo{position:absolute;display:flex;align-items:center;gap:3px;font-family:"Poppins",sans-serif;font-weight:500;font-size:8px;color:#fff;white-space:nowrap}
.logo .dot{width:9px;height:9px;border-radius:50%;background:var(--green)}
.topbar{position:absolute;top:7px;right:30px;display:flex;align-items:center;gap:8px;font-size:3.6px;color:#fff}
.topbar .lang{background:var(--green);padding:2px 5px;border-radius:1px}
.nav{position:absolute;top:25px;right:38px;display:flex;gap:14px;font-size:4.4px;font-weight:500;color:#fff}
.hdr-title{position:absolute;left:0;right:0;top:50px;text-align:center;font-family:"PT Sans Narrow",sans-serif;font-weight:700;font-size:12px;color:#fff;letter-spacing:.2px}
.crumb{position:absolute;left:29px;top:89px;font-size:3.4px;color:var(--muted)}
.crumb b{color:var(--text);font-weight:500}
.h-narrow{font-family:"PT Sans Narrow",sans-serif;font-weight:400;color:var(--ink)}
.sec-title{position:absolute;left:0;width:378px;text-align:center;font-family:"PT Sans Narrow",sans-serif;font-size:11.5px;color:var(--ink)}
.tiny{font-size:3.6px;line-height:5.2px;color:#5c6464}
.btn{display:inline-block;background:var(--green);color:#fff;font-size:3.4px;padding:2.5px 6px;border-radius:1px}
.field{position:absolute;height:10px;border:0.6px solid var(--line);background:#fff;font-size:3.3px;color:var(--muted);padding:3px 4px;display:flex;justify-content:space-between;align-items:center}
.ftr{position:absolute;left:0;width:378px;height:193px;background:var(--dark);color:#fff}
.ftr .f-sub{position:absolute;left:30px;top:52px;font-size:3.6px;font-weight:500;padding-bottom:2px;border-bottom:.6px solid #fff;width:62px}
.ftr .f-arrow{position:absolute;left:100px;top:53px;width:12px;height:4px}
.ftr .f-desc{position:absolute;left:30px;top:64px;width:100px;font-size:3.6px;line-height:5px;color:#cfd3d3}
.ftr .f-col{position:absolute;top:26px}
.ftr h4{font-size:4px;font-weight:500;color:var(--green);margin-bottom:5px}
.ftr .f-col li{font-size:3.6px;color:#d6d9d9;margin-bottom:5.6px}
.ftr .post{display:flex;gap:4px;margin-bottom:9px}
.ftr .post .thumb{width:20px;height:15px;background:linear-gradient(135deg,#7a6a55,#c9a77a)}
.ftr .post p{font-size:3.3px;line-height:4.4px;color:var(--green);font-weight:500;width:72px}
.ftr .post small{display:block;color:#d6d9d9;font-weight:400;margin-top:3px}
.ftr .f-contact{position:absolute;left:30px;right:30px;top:112px;display:flex;justify-content:space-between}
.ftr .ci{display:flex;gap:4px;align-items:center;font-size:3.6px;line-height:4.6px;color:#e3e6e6}
.ftr .ci b{display:block;color:var(--green);font-weight:500}
.ftr .ci svg{width:9px;height:9px}
.ftr .f-legal{position:absolute;left:0;right:0;top:151px;text-align:center;font-size:3.3px;line-height:5px;color:#e3e6e6}
.ftr .f-legal span{color:var(--green)}
.ftr .f-social{position:absolute;left:50%;top:167px;transform:translateX(-50%);display:flex;gap:3px}
.ftr .f-social i{display:block;width:5px;height:5px;border-radius:50%;background:#fff}
.ftr .f-social u{display:block;width:14px;height:5px;border-radius:1px;background:#3b6fd8}
.dest{position:absolute;width:103px}
.dest .ph{position:relative;height:70px}
.dest h5{font-family:"PT Sans Narrow",sans-serif;font-weight:400;font-size:4.6px;color:var(--ink);margin:4px 0 2px}
.dest p{font-size:3.3px;line-height:4.2px;color:#5c6464;margin-bottom:4px}
.tile{position:absolute}
.tile .box{position:absolute;padding:6px 7px;color:#fff}
.tile .box h5{font-family:"PT Sans Narrow",sans-serif;font-weight:400;font-size:7px;margin-bottom:3px;line-height:7px}
.tile .box p{font-size:3px;line-height:4px;margin-bottom:5px}
.tile .btn-w{display:inline-block;border:.5px solid #fff;font-size:3px;padding:2px 4px;background:rgba(255,255,255,.15)}
.post-card{position:absolute;width:112px}
.post-card .ph{position:relative;height:77px}
.post-card .meta{font-size:3px;color:#5c6464;margin:6px 0 4px}
.post-card h5{font-family:"PT Sans Narrow",sans-serif;font-weight:400;font-size:5.6px;line-height:6.4px;color:var(--ink);margin-bottom:4px}
.post-card p{font-size:3.2px;line-height:4.3px;color:#6a7272;margin-bottom:4px}
.side-box{position:absolute;border:.6px solid #e4e8e8;padding:6px 4px;background:#fff}
.side-box h6{font-size:4px;font-weight:500;color:var(--ink);margin-bottom:4px}
.side-box li{font-size:3.2px;color:#5c6464;display:flex;justify-content:space-between;border-bottom:.4px solid #eef0f0;padding:2px 0}
.amen{position:absolute;font-size:3.5px;color:#444;display:flex;align-items:center;gap:3px}
.amen i{width:5px;height:4px;background:var(--green);border-radius:1px;display:block}
.acc{position:absolute;width:60px}
.acc h6{font-size:3.6px;color:var(--green);font-weight:500;text-decoration:underline;margin-bottom:4px}
.acc li{font-size:3.2px;color:#444;display:flex;gap:3px;align-items:center;margin-bottom:3.6px}
.acc li i{width:4px;height:3px;background:var(--green);display:block}
.acc li span{width:26px}
.row-text{position:absolute;width:140px}
.row-text .kick{font-family:"PT Sans Narrow",sans-serif;font-size:5.6px;color:var(--ink)}
.row-text h3{font-family:"PT Sans Narrow",sans-serif;font-weight:400;font-size:11px;line-height:12px;color:var(--ink);margin:1px 0 4px}
.row-text p{font-size:3.3px;line-height:4.6px;color:#6a7272}
</style>
</head>
<body>

<svg width="0" height="0" style="position:absolute" aria-hidden="true">
  <defs>
    <symbol id="i-phone" viewBox="0 0 24 24"><path d="M6.6 10.8a15.1 15.1 0 0 0 6.6 6.6l2.2-2.2a1 1 0 0 1 1-.25 11.4 11.4 0 0 0 3.6.57 1 1 0 0 1 1 1V20a1 1 0 0 1-1 1A17 17 0 0 1 3 4a1 1 0 0 1 1-1h3.5a1 1 0 0 1 1 1c0 1.25.2 2.45.57 3.57a1 1 0 0 1-.25 1z" fill="none" stroke="#1fcb8b" stroke-width="2"/></symbol>
    <symbol id="i-mail" viewBox="0 0 24 24"><rect x="2" y="5" width="20" height="14" rx="1" fill="none" stroke="#1fcb8b" stroke-width="2"/><path d="M2 6l10 7 10-7" fill="none" stroke="#1fcb8b" stroke-width="2"/></symbol>
    <symbol id="i-pin" viewBox="0 0 24 24"><path d="M12 22s-7-7.5-7-13a7 7 0 0 1 14 0c0 5.5-7 13-7 13z" fill="none" stroke="#1fcb8b" stroke-width="2"/><circle cx="12" cy="9" r="2.5" fill="none" stroke="#1fcb8b" stroke-width="2"/></symbol>
    <symbol id="i-arrow" viewBox="0 0 24 8"><path d="M0 4h22M18 1l4 3-4 3" fill="none" stroke="#1fcb8b" stroke-width="1"/></symbol>
  </defs>
</svg>

<div class="board-title" style="left:11px;top:22px">HOME PAGE</div>
<div class="board-title" style="left:411px;top:22px">PROPERTY</div>
<div class="board-title" style="left:811px;top:22px">CUSTOM</div>
<div class="board-title" style="left:411px;top:790px">BLOG</div>
<div class="board-title" style="left:811px;top:976px">BLOG DETAILS</div>
<div class="board-title" style="left:411px;top:1704px">CONTAC US</div>

<!-- ===================== HOME PAGE ===================== -->
<section class="page" style="left:11px;top:67px;height:1841px">
  <div class="ph" role="img" aria-label="Luxury villa with pool and garden at dusk" style="left:0;top:0;width:378px;height:171px;background:linear-gradient(160deg,#1d3550 0%,#3d5d72 35%,#7f8d83 60%,#4c4438 100%)"></div>
  <div class="logo" style="left:37px;top:16px"><span class="dot"></span>VillaHaven</div>
  <div class="topbar" style="right:30px"><span>Login</span><span>Wish List (0)</span><span class="lang">Language</span></div>
  <div class="nav" style="right:40px"><span>Last Minute</span><span>Special Offers</span><span>Experience</span><span>Contact Us</span></div>
  <svg class="abs" style="left:33px;top:158px" width="30" height="6" viewBox="0 0 30 6"><path d="M12 3H1M4 0.5 1 3l3 2.5M18 3h11M26 0.5 29 3l-3 2.5" stroke="#fff" stroke-width=".8" fill="none"/></svg>
  <div class="abs" style="left:225px;top:48px;width:130px;height:123px;background:#fff">
    <div class="abs h-narrow" style="left:10px;top:27px;font-family:Poppins,sans-serif;font-size:5.6px;color:#222">Exclusive Villas in Italy</div>
    <div class="field" style="left:10px;top:40px;width:98px">Destination<svg width="5" height="5"><use href="#i-pin"/></svg></div>
    <div class="field" style="left:10px;top:56px;width:47px">Check In<span>▫</span></div>
    <div class="field" style="left:61px;top:56px;width:47px">Check Out<span>▫</span></div>
    <div class="field" style="left:10px;top:72px;width:98px">Travelers<span>♙</span></div>
    <div class="abs" style="left:10px;top:90px;width:98px;height:13px;background:var(--green);color:#fff;font-size:3.8px;text-align:center;line-height:13px">Search Now</div>
  </div>
  <div class="abs" style="left:350px;top:37px;width:24px;height:24px;border:1.5px solid var(--green);padding:2px"><div style="width:100%;height:100%;background:var(--green)"></div></div>

  <div class="ph" role="img" aria-label="Dark city-skyline photo" style="left:30px;top:202px;width:114px;height:170px;background:linear-gradient(180deg,#2b2f33,#3d4246)"></div>
  <div class="abs" style="left:82px;top:244px;width:93px;height:135px;background:var(--green)"></div>
  <div class="ph" role="img" aria-label="City waterfront and villa terrace photos" style="left:73px;top:235px;width:92px;height:135px;background:linear-gradient(180deg,#b9c7c4 0%,#8f9c84 40%,#d7c2a2 60%,#6d6152 100%)"></div>
  <div class="abs" style="left:189px;top:206px;width:160px">
    <div class="h-narrow" style="font-size:11px;line-height:12px">Looking for an<br>exclusive holiday?</div>
    <p class="tiny" style="margin-top:16px">Browse our vacation rental selections.<br>If you are looking for a real experience, our portal is the right solution.</p>
    <p class="tiny" style="margin-top:5px">Our vacation homes are all located in Italy and we take care of them and their owners at every time. Our goal is to give our guests an authentic taste of holiday and our country.</p>
    <p class="tiny" style="margin-top:5px">Our team is always ready to assure the best time and take care of you!<br>Add a local experience to your stay with us: by diving into our local network you can have the unique chance to discover and travel our culture through the eye of a local…</p>
  </div>

  <div class="sec-title" style="top:410px">Destinations &amp; Tourist Areas</div>
  <div class="dest" style="left:30px;top:427px"><div class="ph" role="img" aria-label="Roman Colosseum" style="background:linear-gradient(180deg,#9bb4c9,#a88a6a 60%,#6f5a45)"></div><h5>Roman Coliseum</h5><p>If you use this site regularly and would like to help keep the site on the Internet</p><span class="btn">View More</span></div>
  <div class="dest" style="left:137px;top:427px"><div class="ph" role="img" aria-label="Canal of a city" style="background:linear-gradient(180deg,#8fb3cf,#b88a6a 50%,#3f6f74)"></div><h5>Canal of a City</h5><p>If you use this site regularly and would like to help keep the site on the Internet</p><span class="btn">View More</span></div>
  <div class="dest" style="left:245px;top:427px"><div class="ph" role="img" aria-label="Venice waterfront" style="background:linear-gradient(180deg,#9fbcd3,#c9b59a 50%,#4a6d7a)"></div><h5>Venice Italy</h5><p>If you use this site regularly and would like to help keep the site on the Internet</p><span class="btn">View More</span></div>
  <div class="dest" style="left:30px;top:546px"><div class="ph" role="img" aria-label="Petra rock temple" style="background:linear-gradient(180deg,#b98a66,#8c5c3e)"></div><h5>Petra Ulum in Jordan</h5><p>If you use this site regularly and would like to help keep the site on the Internet</p><span class="btn">View More</span></div>
  <div class="dest" style="left:137px;top:546px"><div class="ph" role="img" aria-label="Leaning tower" style="background:linear-gradient(180deg,#3d7fd0,#9fc3e6 50%,#e4ddcf)"></div><h5>Tower of Pisa</h5><p>If you use this site regularly and would like to help keep the site on the Internet</p><span class="btn">View More</span></div>
  <div class="dest" style="left:245px;top:546px"><div class="ph" role="img" aria-label="Vatican basilica at dusk" style="background:linear-gradient(180deg,#1d2a4a,#3a3f5a 50%,#c9a058)"></div><h5>Vatican Building at Dusk</h5><p>If you use this site regularly and would like to help keep the site on the Internet</p><span class="btn">View More</span></div>

  <div class="abs" style="left:0;top:684px;width:378px;height:54px;background:#f3f5f5"></div>
  <div class="sec-title" style="top:692px;font-size:6px">New Villas &amp;</div>
  <div class="sec-title" style="top:700px">Vacation Rentals</div>
  <div class="ph" role="img" aria-label="Villa with swimming pool" style="left:0;top:736px;width:94px;height:90px;background:linear-gradient(180deg,#8cb6d8,#d9d3c6 50%,#4aa6c9)"></div>
  <div class="ph" role="img" aria-label="White Mediterranean villa" style="left:94px;top:736px;width:95px;height:90px;background:linear-gradient(180deg,#5d9ed8,#e8e4dc 55%,#5a8b55)"></div>
  <div class="ph" role="img" aria-label="Villa at night" style="left:189px;top:736px;width:95px;height:90px;background:linear-gradient(180deg,#1f2224,#3a3630)"></div>
  <div class="abs" style="left:196px;top:768px;color:#fff">
    <div style="font-family:'PT Sans Narrow',sans-serif;font-size:6px">Podere Le Querce</div>
    <div style="font-size:3px;line-height:4.5px;margin-top:3px">Sleeps &nbsp;&nbsp;&nbsp;&nbsp;&nbsp;&nbsp; 27<br>Bedrooms &nbsp;&nbsp; 9</div>
    <span class="btn" style="margin-top:3px">View More</span>
  </div>
  <div class="ph" role="img" aria-label="Guest relaxing in pool" style="left:284px;top:736px;width:94px;height:90px;background:linear-gradient(180deg,#c9a17a,#4fb4c2 55%,#2d8aa3)"></div>

  <div class="tile ph" role="img" aria-label="Florence rooftops and cathedral dome" style="left:30px;top:843px;width:155px;height:116px;background:linear-gradient(160deg,#a97653,#c98f62 50%,#6c4a37)"></div>
  <div class="tile" style="left:30px;top:843px"><div class="box" style="left:6px;top:18px;width:60px;height:78px;background:#0d0d0d"><h5>Luxury Villas</h5><p>This selection of properties includes all the best rentals available. Most with private swimming pool with chef and maid services available.</p><span class="btn" style="font-size:3px">View Details</span></div></div>
  <div class="tile ph" role="img" aria-label="Fresh salad bowl" style="left:189px;top:843px;width:159px;height:116px;background:linear-gradient(150deg,#5d7a3a,#9bb34f 45%,#c7533a 75%,#3e4a2b)"></div>
  <div class="tile" style="left:189px;top:843px"><div class="box" style="left:6px;top:20px;width:72px;height:52px;background:var(--green)"><h5>Experiences</h5><p>Don't be just a holiday but an experience! Let's discover our services</p><span class="btn-w">View Details</span></div></div>
  <div class="tile ph" role="img" aria-label="Traveller celebrating on a beach" style="left:30px;top:963px;width:155px;height:115px;background:linear-gradient(180deg,#5fb0e4,#a8d6ef 45%,#e2cfa8)"></div>
  <div class="tile" style="left:30px;top:963px"><div class="box" style="left:6px;top:21px;width:68px;height:70px;background:var(--green)"><h5>Browse All Vacation Rentals</h5><p>From here you can browse all the villa selections, you can refine them by using the filters on the search results web page.</p><span class="btn-w" style="background:#fff;color:var(--green)">View Details</span></div></div>
  <div class="tile ph" role="img" aria-label="Suitcase with travel stickers" style="left:189px;top:963px;width:159px;height:115px;background:linear-gradient(150deg,#0b2a4a,#1d4f7a 55%,#c23a3a 80%,#1b2c3f)"></div>
  <div class="tile" style="left:189px;top:963px"><div class="box" style="left:6px;top:22px;width:62px;height:70px;background:#10294a"><h5>Last Minute Deals</h5><p>Browse all the last minute deals to browse the villas offering discounts for last minute arrivals. Save money by checking these offers</p><span class="btn">View Details</span></div></div>

  <div class="sec-title" style="top:1107px">Testimonials</div>
  <div class="ph" role="img" aria-label="Villa exterior under evening sky" style="left:0;top:1132px;width:378px;height:134px;background:linear-gradient(180deg,#13305a,#2c5788 60%,#6f7b85)"></div>
  <div class="abs" style="left:272px;top:1282px;width:86px;height:66px;background:repeating-linear-gradient(45deg,#eef0f0 0 1px,#fff 1px 3px)"></div>
  <div class="abs" style="left:55px;top:1191px;width:280px;height:152px;background:#fff;text-align:center">
    <div style="position:absolute;left:36px;top:14px;font-family:Georgia,serif;font-size:24px;color:#555;line-height:1">“</div>
    <p style="position:absolute;left:34px;right:34px;top:37px;font-size:4.6px;line-height:7.6px;color:#444">Lorem Ipsum is simply dummy text of the printing and typesetting industry. Lorem Ipsum has been the industry's standard dummy text ever since the 1500s, when an unknown printer took a galley of type and scrambled it to make a type specimen book. It has survived not only five ce</p>
    <div style="position:absolute;right:36px;top:70px;font-family:Georgia,serif;font-size:24px;color:#d8dada;line-height:1">”</div>
    <div style="position:absolute;left:132px;top:92px;width:17px;height:17px;border-radius:50%;background:#cfd6dc"></div>
    <div style="position:absolute;left:0;right:0;top:113px;font-size:4.4px;color:#333">Marco Bellini</div>
    <div style="position:absolute;left:0;right:0;top:120px;font-size:6px;color:#333">‹ ›</div>
  </div>

  <div class="abs" style="left:0;top:1370px;width:378px;height:40px;background:#f6f7f7"></div>
  <div class="sec-title" style="top:1384px">Recent Blog</div>
  <div class="dest" style="left:30px;top:1405px"><div class="ph" role="img" aria-label="Hotel reception desk" style="height:60px;background:linear-gradient(150deg,#8a3d32,#c98d63 50%,#e4c8a4)"></div><h5 style="font-size:4.6px">Quis autem vel eum iure reprehenderit qui in ea voluptate</h5><span class="btn">Read More</span></div>
  <div class="dest" style="left:137px;top:1405px"><div class="ph" role="img" aria-label="Restaurant table setting" style="height:60px;background:linear-gradient(150deg,#6f4628,#d3a26c 50%,#f0e2c8)"></div><h5 style="font-size:4.6px">Quis autem vel eum iure reprehenderit qui in ea voluptate</h5><span class="btn">Read More</span></div>
  <div class="dest" style="left:245px;top:1405px"><div class="ph" role="img" aria-label="Seaside resort town" style="height:60px;background:linear-gradient(180deg,#9fc8e8,#e6dcc9 50%,#4d9bbf)"></div><h5 style="font-size:4.6px">Quis autem vel eum iure reprehenderit qui in ea voluptate</h5><span class="btn">Read More</span></div>

  <div class="sec-title" style="top:1536px">Quick Contact</div>
  <div class="field" style="left:98px;top:1556px;width:62px;height:9px">Name</div>
  <div class="field" style="left:162px;top:1556px;width:62px;height:9px">Email</div>
  <div class="field" style="left:226px;top:1556px;width:62px;height:9px">Phone</div>
  <div class="field" style="left:98px;top:1568px;width:190px;height:34px;align-items:flex-start">Message</div>
  <div class="abs btn" style="left:264px;top:1607px">Submit</div>

  <footer class="ftr" style="top:1648px">
    <div class="logo" style="left:30px;top:31px"><span class="dot"></span>VillaHaven</div>
    <div class="f-sub">Subscribe to our Newsletter</div>
    <svg class="f-arrow" viewBox="0 0 24 8"><use href="#i-arrow"/></svg>
    <p class="f-desc">Our range of services is very large, and we are constantly expanding it.</p>
    <div class="f-col" style="left:162px"><h4>Navigation</h4><ul><li>Last Minute</li><li>Special Offers</li><li>Experience</li><li>Contact Us</li></ul></div>
    <div class="f-col" style="left:249px"><h4>Recent posts</h4><div class="post"><div class="thumb"></div><p>Which construction tool is better to choose?<small>2 November, 2020</small></p></div><div class="post"><div class="thumb"></div><p>Which construction tool is better to choose?<small>2 November, 2020</small></p></div></div>
    <div class="f-contact"><div class="ci"><svg><use href="#i-phone"/></svg><div><b>Call us</b>+1 555 010 2040 (USA)</div></div><div class="ci"><svg><use href="#i-mail"/></svg><div><b>Write to us</b>sales@example.com</div></div><div class="ci"><svg><use href="#i-pin"/></svg><div><b>Office location</b>12 Olive Grove Rd, Lakeside</div></div></div>
    <div class="f-legal">Privacy Policies &nbsp;/&nbsp; Reservation Policies &nbsp;/&nbsp; Cookie Policy<br>Copyright © 2021 VillaHaven. All Rights Reserved. <span>Powered by VillaHaven</span></div>
    <div class="f-social"><i></i><u></u></div>
  </footer>
</section>

<!-- ===================== PROPERTY ===================== -->
<section class="page" style="left:411px;top:67px;height:694px">
  <div class="hdr"><div class="ph" role="img" aria-label="Villa pool at dusk" style="left:0;top:0;width:378px;height:76px;background:linear-gradient(180deg,#1f3a40,#2f6167 60%,#1a2c30)"></div>
    <div class="logo" style="left:30px;top:12px"><span class="dot"></span>VillaHaven</div>
    <div class="topbar"><span>Login</span><span>Wish List (0)</span><span class="lang">Language</span></div>
    <div class="nav"><span>Last Minute</span><span>Special Offers</span><span>Experience</span><span>Contact Us</span></div>
    <div class="hdr-title">PROPERTY</div>
    <div class="abs" style="left:30px;top:65px;background:#fff;border-radius:5px;font-size:3.4px;padding:1.5px 6px">Photo Gallery</div>
    <div class="abs" style="left:334px;top:63px;width:12px;height:12px;border-radius:50%;border:.7px solid #fff"></div>
  </div>
  <div class="crumb">Home Page / Italy / Tuscany / Toscana / Casa Valle Verde / <b>Agriturismo Il Poggio</b></div>
  <div class="abs h-narrow" style="left:30px;top:105px;font-size:11px;font-weight:700">Agriturismo Il Poggio</div>
  <div class="abs" style="left:30px;top:120px;font-size:3.4px;line-height:5px;color:#444">Country House / Farm House<br><span style="color:var(--muted)">Accommodations: 2 Sleeps: 7 Bedrooms: 2 Bathrooms: 2</span></div>
  <div class="abs h-narrow" style="left:30px;top:148px;font-size:6.6px">Description</div>
  <p class="abs tiny" style="left:30px;top:160px;width:205px;font-size:3.3px;line-height:5px">The farmhouse sits among quiet hills in the countryside, only a short drive from the nearest village where you will find shops and all daily services. The pool is shared by the two apartments, measures 5x9 metres, is fenced and open every day from morning until evening. Both apartments can be booked together for full privacy and total independence during your stay.</p>
  <div class="abs" style="left:254px;top:110px;width:101px;height:111px;background:var(--green)"></div>
  <div class="abs" style="left:249px;top:105px;width:101px;height:111px;background:#fff;border:.6px solid #e6eaea">
    <div class="field" style="left:7px;top:7px;width:86px;height:9px">Accommodation<span>▾</span></div>
    <div class="field" style="left:7px;top:23px;width:86px;height:9px">Check In<span>▫</span></div>
    <div class="field" style="left:7px;top:39px;width:86px;height:9px">Check Out<span>▫</span></div>
    <div class="field" style="left:7px;top:55px;width:40px;height:9px">Travelers<span>♙</span></div>
    <div class="field" style="left:53px;top:55px;width:40px;height:9px">Pets<span>▾</span></div>
    <div class="abs" style="left:7px;top:72px;width:86px;height:11px;background:var(--green);color:#fff;font-size:3.4px;text-align:center;line-height:11px">Book Now</div>
    <div class="abs" style="left:7px;top:86px;width:86px;height:11px;background:#3a3d3e;color:#fff;font-size:3.4px;text-align:center;line-height:11px">Info Request</div>
  </div>
  <div class="abs h-narrow" style="left:30px;top:201px;font-size:6.6px">Amenities</div>
  <div class="abs" style="left:198px;top:203px;display:flex;gap:2.5px"><i style="width:4px;height:4px;background:var(--green);display:block"></i><i style="width:4px;height:4px;background:var(--green);display:block;border-radius:50%"></i><i style="width:4px;height:4px;background:var(--green);display:block;border-radius:50%"></i><i style="width:4px;height:4px;background:var(--green);display:block;border-radius:50%"></i><i style="width:4px;height:4px;background:var(--green);display:block;border-radius:50%"></i></div>
  <div class="amen" style="left:30px;top:219px"><i></i>Garden</div>
  <div class="amen" style="left:114px;top:219px"><i></i>Near Village</div>
  <div class="amen" style="left:199px;top:219px"><i></i>Internet</div>
  <div class="amen" style="left:30px;top:231px"><i></i>Baby Bed</div>
  <div class="amen" style="left:114px;top:231px"><i></i>Maid</div>
  <div class="amen" style="left:199px;top:231px"><i></i>Parking</div>
  <div class="amen" style="left:30px;top:243px"><i></i>Swimmingpool</div>
  <div class="amen" style="left:114px;top:243px"><i></i>Wedding</div>
  <div class="amen" style="left:199px;top:243px"><i></i>Breakfast</div>
  <div class="amen" style="left:30px;top:254px"><i></i>Internet Wifi</div>
  <div class="abs h-narrow" style="left:30px;top:275px;font-size:6.6px">Gallery</div>
  <div class="ph" role="img" aria-label="Modern villa with pool" style="left:30px;top:289px;width:85px;height:52px;background:linear-gradient(180deg,#7fa8c9,#d8d4cc 50%,#3f8fb2)"></div>
  <div class="abs h-narrow" style="left:166px;top:275px;font-size:6.6px">Accommodations</div>
  <div class="acc" style="left:166px;top:288px"><h6>Casa Ginestra</h6><ul><li><i></i><span>Sleeps</span>4</li><li><i></i><span>Bed Room</span>1</li><li><i></i><span>Bathroom</span>1</li></ul><span class="btn" style="font-size:3px">View Details</span></div>
  <div class="acc" style="left:235px;top:288px"><h6>Casa Lavanda</h6><ul><li><i></i><span>Sleeps</span>3</li><li><i></i><span>Bed Room</span>1</li><li><i></i><span>Bathroom</span>1</li></ul><span class="btn" style="font-size:3px">View Details</span></div>
  <div class="ph" role="img" aria-label="Map of Italy showing the property location" style="left:30px;top:372px;width:318px;height:113px;background:linear-gradient(135deg,#aadaff 0%,#aadaff 25%,#cfe8c4 35%,#e9eedf 55%,#aadaff 70%,#d7ecc9 85%)"></div>

  <footer class="ftr" style="top:501px">
    <div class="logo" style="left:30px;top:31px"><span class="dot"></span>VillaHaven</div>
    <div class="f-sub">Subscribe to our Newsletter</div>
    <svg class="f-arrow" viewBox="0 0 24 8"><use href="#i-arrow"/></svg>
    <p class="f-desc">Our range of services is very large, and we are constantly expanding it.</p>
    <div class="f-col" style="left:162px"><h4>Navigation</h4><ul><li>Last Minute</li><li>Special Offers</li><li>Experience</li><li>Contact Us</li></ul></div>
    <div class="f-col" style="left:249px"><h4>Recent posts</h4><div class="post"><div class="thumb"></div><p>Which construction tool is better to choose?<small>2 November, 2020</small></p></div><div class="post"><div class="thumb"></div><p>Which construction tool is better to choose?<small>2 November, 2020</small></p></div></div>
    <div class="f-contact"><div class="ci"><svg><use href="#i-phone"/></svg><div><b>Call us</b>+1 555 010 2040 (USA)</div></div><div class="ci"><svg><use href="#i-mail"/></svg><div><b>Write to us</b>sales@example.com</div></div><div class="ci"><svg><use href="#i-pin"/></svg><div><b>Office location</b>12 Olive Grove Rd, Lakeside</div></div></div>
    <div class="f-legal">Privacy Policies &nbsp;/&nbsp; Reservation Policies &nbsp;/&nbsp; Cookie Policy<br>Copyright © 2021 VillaHaven. All Rights Reserved. <span>Powered by VillaHaven</span></div>
    <div class="f-social"><i></i><u></u></div>
  </footer>
</section>

<!-- ===================== BLOG ===================== -->
<section class="page" style="left:411px;top:836px;height:847px">
  <div class="hdr"><div class="ph" role="img" aria-label="Old castle on a hill" style="left:0;top:0;width:378px;height:76px;background:linear-gradient(180deg,#5b6a70,#3f4a4a 60%,#2e3a30)"></div>
    <div class="logo" style="left:30px;top:12px"><span class="dot"></span>VillaHaven</div>
    <div class="topbar"><span>Login</span><span>Wish List (0)</span><span class="lang">Language</span></div>
    <div class="nav"><span>Last Minute</span><span>Special Offers</span><span>Experience</span><span>Contact Us</span></div>
    <div class="hdr-title">BLOG</div>
  </div>
  <div class="crumb">Home Page / <b>Blog</b></div>
  <div class="abs h-narrow" style="left:30px;top:107px;font-size:11px">Blog</div>

  <div class="post-card" style="left:30px;top:130px"><div class="ph" role="img" aria-label="Hotel reception desk" style="background:linear-gradient(150deg,#8a3d32,#c98d63 50%,#e4c8a4)"></div><div class="meta">Jhon Doe &nbsp;|&nbsp; December 4, 2020 &nbsp;|&nbsp; 0 Comments</div><h5>One who avoids a pain that produces no resultant pleasure</h5><p>Nam libero tempore, cum soluta nobis est eligendi optio cumque nihil impedit quo minus id quod maxime placeat facere possimus, omnis voluptas assumenda est, omnis dolor repellendus.</p><span class="btn">Read More</span></div>
  <div class="post-card" style="left:147px;top:130px"><div class="ph" role="img" aria-label="Restaurant table setting" style="background:linear-gradient(150deg,#6f4628,#d3a26c 50%,#f0e2c8)"></div><div class="meta">Jhon Doe &nbsp;|&nbsp; December 4, 2020 &nbsp;|&nbsp; 0 Comments</div><h5>One who avoids a pain that produces no resultant pleasure</h5><p>Nam libero tempore, cum soluta nobis est eligendi optio cumque nihil impedit quo minus id quod maxime placeat facere possimus, omnis voluptas assumenda est, omnis dolor repellendus.</p><span class="btn">Read More</span></div>
  <div class="post-card" style="left:30px;top:300px"><div class="ph" role="img" aria-label="Guest relaxing in pool" style="background:linear-gradient(180deg,#c9a17a,#4fb4c2 55%,#2d8aa3)"></div><div class="meta">Jhon Doe &nbsp;|&nbsp; December 4, 2020 &nbsp;|&nbsp; 0 Comments</div><h5>One who avoids a pain that produces no resultant pleasure</h5><p>Nam libero tempore, cum soluta nobis est eligendi optio cumque nihil impedit quo minus id quod maxime placeat facere possimus, omnis voluptas assumenda est, omnis dolor repellendus.</p><span class="btn">Read More</span></div>
  <div class="post-card" style="left:147px;top:300px"><div class="ph" role="img" aria-label="Basilica at night" style="background:linear-gradient(180deg,#1d2a4a,#3a3f5a 50%,#c9a058)"></div><div class="meta">Jhon Doe &nbsp;|&nbsp; December 4, 2020 &nbsp;|&nbsp; 0 Comments</div><h5>One who avoids a pain that produces no resultant pleasure</h5><p>Nam libero tempore, cum soluta nobis est eligendi optio cumque nihil impedit quo minus id quod maxime placeat facere possimus, omnis voluptas assumenda est, omnis dolor repellendus.</p><span class="btn">Read More</span></div>
  <div class="post-card" style="left:30px;top:477px"><div class="ph" role="img" aria-label="Venetian-style canal mall" style="background:linear-gradient(180deg,#7fa2c4,#c4b39a 55%,#4b6a7d)"></div><div class="meta">Jhon Doe &nbsp;|&nbsp; December 4, 2020 &nbsp;|&nbsp; 0 Comments</div><h5>One who avoids a pain that produces no resultant pleasure</h5><p>Nam libero tempore, cum soluta nobis est eligendi optio cumque nihil impedit quo minus id quod maxime placeat facere possimus, omnis voluptas assumenda est, omnis dolor repellendus.</p><span class="btn">Read More</span></div>
  <div class="post-card" style="left:147px;top:477px"><div class="ph" role="img" aria-label="Bedroom with sea view" style="background:linear-gradient(180deg,#6e8fa6,#c8ced2 55%,#8a7a68)"></div><div class="meta">Jhon Doe &nbsp;|&nbsp; December 4, 2020 &nbsp;|&nbsp; 0 Comments</div><h5>One who avoids a pain that produces no resultant pleasure</h5><p>Nam libero tempore, cum soluta nobis est eligendi optio cumque nihil impedit quo minus id quod maxime placeat facere possimus, omnis voluptas assumenda est, omnis dolor repellendus.</p><span class="btn">Read More</span></div>

  <div class="side-box" style="left:283px;top:110px;width:64px"><h6>CATEGORIES</h6><ul><li>Consectetur Adipiscing<span>›</span></li><li>Eget Tempor<span>›</span></li><li>Lobortis Dictum<span>›</span></li><li>Tempus Fermentum<span>›</span></li><li>Quisque<span>›</span></li><li>Consectetur Adipiscing<span>›</span></li><li>Eget Tempor<span>›</span></li><li>Lobortis Dictum<span>›</span></li><li>Tempus Fermentum<span>›</span></li><li>Quisque<span>›</span></li></ul></div>

  <footer class="ftr" style="top:654px">
    <div class="logo" style="left:30px;top:31px"><span class="dot"></span>VillaHaven</div>
    <div class="f-sub">Subscribe to our Newsletter</div>
    <svg class="f-arrow" viewBox="0 0 24 8"><use href="#i-arrow"/></svg>
    <p class="f-desc">Our range of services is very large, and we are constantly expanding it.</p>
    <div class="f-col" style="left:162px"><h4>Navigation</h4><ul><li>Last Minute</li><li>Special Offers</li><li>Experience</li><li>Contact Us</li></ul></div>
    <div class="f-col" style="left:249px"><h4>Recent posts</h4><div class="post"><div class="thumb"></div><p>Which construction tool is better to choose?<small>2 November, 2020</small></p></div><div class="post"><div class="thumb"></div><p>Which construction tool is better to choose?<small>2 November, 2020</small></p></div></div>
    <div class="f-contact"><div class="ci"><svg><use href="#i-phone"/></svg><div><b>Call us</b>+1 555 010 2040 (USA)</div></div><div class="ci"><svg><use href="#i-mail"/></svg><div><b>Write to us</b>sales@example.com</div></div><div class="ci"><svg><use href="#i-pin"/></svg><div><b>Office location</b>12 Olive Grove Rd, Lakeside</div></div></div>
    <div class="f-legal">Privacy Policies &nbsp;/&nbsp; Reservation Policies &nbsp;/&nbsp; Cookie Policy<br>Copyright © 2021 VillaHaven. All Rights Reserved. <span>Powered by VillaHaven</span></div>
    <div class="f-social"><i></i><u></u></div>
  </footer>
</section>

<!-- ===================== CONTACT US ===================== -->
<section class="page" style="left:411px;top:1747px;height:598px">
  <div class="hdr"><div class="ph" role="img" aria-label="Harbour with boats" style="left:0;top:0;width:378px;height:76px;background:linear-gradient(180deg,#4f5a5e,#3a4446 55%,#24302f)"></div>
    <div class="logo" style="left:30px;top:12px"><span class="dot"></span>VillaHaven</div>
    <div class="topbar"><span>Login</span><span>Wish List (0)</span><span class="lang">Language</span></div>
    <div class="nav"><span>Last Minute</span><span>Special Offers</span><span>Experience</span><span>Contact Us</span></div>
    <div class="hdr-title">CONTACT US</div>
  </div>
  <div class="crumb">Home Page / <b>Contact Us</b></div>
  <div class="abs h-narrow" style="left:30px;top:107px;font-size:11px">Contact Us</div>
  <p class="abs tiny" style="left:30px;top:124px;width:210px;font-size:3.3px;line-height:4.8px">Use this form to contact us regarding any topics other than specific property requests which should be done using the form on the property detail pages.</p>
  <div class="abs h-narrow" style="left:30px;top:140px;font-size:6.6px">VillaHaven</div>
  <ul class="abs" style="left:30px;top:152px;font-size:3.2px;line-height:4.4px;color:#444;width:100px">
    <li style="display:flex;gap:3px;margin-bottom:5px"><svg width="4" height="4"><use href="#i-pin"/></svg><span>Via dei Cipressi 8, 50100<br>Valdarno, Italy</span></li>
    <li style="display:flex;gap:3px;margin-bottom:5px"><svg width="4" height="4"><use href="#i-phone"/></svg>Phone: +39 000 123 4567</li>
    <li style="display:flex;gap:3px;margin-bottom:5px"><svg width="4" height="4"><use href="#i-mail"/></svg>Fax: +39 000 765 4321</li>
    <li style="display:flex;gap:3px"><svg width="4" height="4"><use href="#i-pin"/></svg>VAT Code: IT00000000000</li>
  </ul>
  <div class="field" style="left:154px;top:155px;width:63px;height:9px">First Name</div>
  <div class="field" style="left:220px;top:155px;width:63px;height:9px">Last Name</div>
  <div class="field" style="left:286px;top:155px;width:62px;height:9px">Country</div>
  <div class="field" style="left:154px;top:168px;width:63px;height:9px">Email</div>
  <div class="field" style="left:220px;top:168px;width:63px;height:9px">Confirm Email</div>
  <div class="field" style="left:286px;top:168px;width:62px;height:9px">Phone</div>
  <div class="field" style="left:154px;top:181px;width:194px;height:33px;align-items:flex-start">Message</div>
  <div class="abs" style="left:154px;top:219px;font-size:3px;color:#555;display:flex;gap:2px;align-items:center"><i style="width:3px;height:3px;border:.4px solid #999;display:block"></i>I would like to subscribe to your newsletter</div>
  <div class="abs" style="left:154px;top:226px;width:47px;height:12px;border:.5px solid #d3d3d3;background:#f9f9f9;font-size:2.8px;color:#555;padding:4px 3px">I'm not a robot</div>
  <div class="abs btn" style="left:154px;top:243px">Send</div>
  <div class="ph" role="img" aria-label="Street map of the office area" style="left:0;top:273px;width:378px;height:131px;background:linear-gradient(160deg,#eef0ea 0%,#e8ebe4 60%,#cfe3f3 75%,#9fc9ee 90%)"></div>

  <footer class="ftr" style="top:405px">
    <div class="logo" style="left:30px;top:31px"><span class="dot"></span>VillaHaven</div>
    <div class="f-sub">Subscribe to our Newsletter</div>
    <svg class="f-arrow" viewBox="0 0 24 8"><use href="#i-arrow"/></svg>
    <p class="f-desc">Our range of services is very large, and we are constantly expanding it.</p>
    <div class="f-col" style="left:162px"><h4>Navigation</h4><ul><li>Last Minute</li><li>Special Offers</li><li>Experience</li><li>Contact Us</li></ul></div>
    <div class="f-col" style="left:249px"><h4>Recent posts</h4><div class="post"><div class="thumb"></div><p>Which construction tool is better to choose?<small>2 November, 2020</small></p></div><div class="post"><div class="thumb"></div><p>Which construction tool is better to choose?<small>2 November, 2020</small></p></div></div>
    <div class="f-contact"><div class="ci"><svg><use href="#i-phone"/></svg><div><b>Call us</b>+1 555 010 2040 (USA)</div></div><div class="ci"><svg><use href="#i-mail"/></svg><div><b>Write to us</b>sales@example.com</div></div><div class="ci"><svg><use href="#i-pin"/></svg><div><b>Office location</b>12 Olive Grove Rd, Lakeside</div></div></div>
    <div class="f-legal">Privacy Policies &nbsp;/&nbsp; Reservation Policies &nbsp;/&nbsp; Cookie Policy<br>Copyright © 2021 VillaHaven. All Rights Reserved. <span>Powered by VillaHaven</span></div>
    <div class="f-social"><i></i><u></u></div>
  </footer>
</section>

<!-- ===================== CUSTOM PAGE ===================== -->
<section class="page" style="left:811px;top:67px;height:862px">
  <div class="hdr"><div class="ph" role="img" aria-label="Venice canal with boats" style="left:0;top:0;width:378px;height:76px;background:linear-gradient(180deg,#5b666b,#3e4a4c 55%,#2a3838)"></div>
    <div class="logo" style="left:30px;top:12px"><span class="dot"></span>VillaHaven</div>
    <div class="topbar"><span>Login</span><span>Wish List (0)</span><span class="lang">Language</span></div>
    <div class="nav"><span>Last Minute</span><span>Special Offers</span><span>Experience</span><span>Contact Us</span></div>
    <div class="hdr-title">CUSTOM PAGE</div>
  </div>
  <div class="crumb">Home Page / <b>Custom Page</b></div>

  <div class="row-text" style="left:29px;top:108px;width:175px"><div class="kick">But I must explain to you</div><h3>How all this mistaken idea<br>of Denouncing</h3><p>Nam libero tempore, cum soluta nobis est eligendi optio cumque nihil impedit quo minus id quod maxime placeat facere possimus, omnis voluptas assumenda est, omnis dolor repellendus. Temporibus autem quibusdam et aut officiis debitis aut rerum necessitatibus saepe eveniet ut et voluptates repudiandae sint et molestiae non recusandae. Itaque earum rerum hic tenetur a sapiente delectus, ut aut reiciendis voluptatibus maiores alias consequatur aut perferendis doloribus asperiores repellat.</p></div>
  <div class="ph" role="img" aria-label="Basilica illuminated at night" style="left:212px;top:110px;width:135px;height:91px;background:linear-gradient(180deg,#1b2440,#3a3b52 45%,#c9a058 75%,#2a2a30)"></div>
  <p class="abs row-text" style="left:29px;top:208px;width:318px;font-size:3.3px;line-height:4.6px;color:#6a7272">Nam libero tempore, cum soluta nobis est eligendi optio cumque nihil impedit quo minus id quod maxime placeat facere possimus, omnis voluptas assumenda est, omnis dolor repellendus. Temporibus autem quibusdam et aut officiis debitis aut rerum necessitatibus saepe eveniet ut et voluptates repudiandae sint et molestiae non recusandae. Itaque earum rerum hic tenetur.</p>

  <div class="ph" role="img" aria-label="Leaning tower under blue sky" style="left:29px;top:240px;width:135px;height:91px;background:linear-gradient(180deg,#3f83d4,#a9cdee 50%,#e5dfd2 80%,#6d8c5a)"></div>
  <div class="row-text" style="left:174px;top:254px;width:173px"><div class="kick">I explain to you</div><h3>Ducimus Qui Praesentium</h3><p>Nam libero tempore, cum soluta nobis est eligendi optio cumque nihil impedit quo minus id quod maxime placeat facere possimus, omnis voluptas assumenda est, omnis dolor repellendus. Temporibus autem quibusdam et aut officiis debitis aut rerum necessitatibus saepe eveniet ut et voluptates repudiandae sint et molestiae non recusandae.</p></div>

  <div class="row-text" style="left:29px;top:356px;width:173px"><div class="kick">I explain to you</div><h3>Ducimus Qui Praesentium</h3><p>Nam libero tempore, cum soluta nobis est eligendi optio cumque nihil impedit quo minus id quod maxime placeat facere possimus, omnis voluptas assumenda est, omnis dolor repellendus. Temporibus autem quibusdam et aut officiis debitis aut rerum necessitatibus saepe eveniet ut et voluptates repudiandae sint et molestiae non recusandae.</p></div>
  <div class="ph" role="img" aria-label="Guest relaxing in pool" style="left:212px;top:342px;width:135px;height:91px;background:linear-gradient(180deg,#c9a17a,#4fb4c2 55%,#2d8aa3)"></div>

  <div class="ph" role="img" aria-label="Roman Colosseum" style="left:29px;top:450px;width:135px;height:91px;background:linear-gradient(180deg,#9bb4c9,#a88a6a 60%,#6f5a45)"></div>
  <div class="row-text" style="left:174px;top:462px;width:173px"><div class="kick">I explain to you</div><h3>Ducimus Qui Praesentium</h3><p>Nam libero tempore, cum soluta nobis est eligendi optio cumque nihil impedit quo minus id quod maxime placeat facere possimus, omnis voluptas assumenda est, omnis dolor repellendus. Temporibus autem quibusdam et aut officiis debitis aut rerum necessitatibus saepe eveniet ut et voluptates repudiandae sint et molestiae non recusandae.</p></div>

  <div class="row-text" style="left:29px;top:567px;width:173px"><div class="kick">I explain to you</div><h3>Ducimus Qui Praesentium</h3><p>Nam libero tempore, cum soluta nobis est eligendi optio cumque nihil impedit quo minus id quod maxime placeat facere possimus, omnis voluptas assumenda est, omnis dolor repellendus. Temporibus autem quibusdam et aut officiis debitis aut rerum necessitatibus saepe eveniet ut et voluptates repudiandae sint et molestiae non recusandae.</p></div>
  <div class="ph" role="img" aria-label="Lakeside mountain village" style="left:212px;top:553px;width:135px;height:91px;background:linear-gradient(180deg,#6fa0cf,#4c7a6a 50%,#2f5a4a 75%,#b98a6a)"></div>

  <footer class="ftr" style="top:668px">
    <div class="logo" style="left:30px;top:31px"><span class="dot"></span>VillaHaven</div>
    <div class="f-sub">Subscribe to our Newsletter</div>
    <svg class="f-arrow" viewBox="0 0 24 8"><use href="#i-arrow"/></svg>
    <p class="f-desc">Our range of services is very large, and we are constantly expanding it.</p>
    <div class="f-col" style="left:162px"><h4>Navigation</h4><ul><li>Last Minute</li><li>Special Offers</li><li>Experience</li><li>Contact Us</li></ul></div>
    <div class="f-col" style="left:249px"><h4>Recent posts</h4><div class="post"><div class="thumb"></div><p>Which construction tool is better to choose?<small>2 November, 2020</small></p></div><div class="post"><div class="thumb"></div><p>Which construction tool is better to choose?<small>2 November, 2020</small></p></div></div>
    <div class="f-contact"><div class="ci"><svg><use href="#i-phone"/></svg><div><b>Call us</b>+1 555 010 2040 (USA)</div></div><div class="ci"><svg><use href="#i-mail"/></svg><div><b>Write to us</b>sales@example.com</div></div><div class="ci"><svg><use href="#i-pin"/></svg><div><b>Office location</b>12 Olive Grove Rd, Lakeside</div></div></div>
    <div class="f-legal">Privacy Policies &nbsp;/&nbsp; Reservation Policies &nbsp;/&nbsp; Cookie Policy<br>Copyright © 2021 VillaHaven. All Rights Reserved. <span>Powered by VillaHaven</span></div>
    <div class="f-social"><i></i><u></u></div>
  </footer>
</section>

<!-- ===================== BLOG DETAILS ===================== -->
<section class="page" style="left:811px;top:1023px;height:686px">
  <div class="hdr"><div class="ph" role="img" aria-label="Old castle on a hill" style="left:0;top:0;width:378px;height:76px;background:linear-gradient(180deg,#5b6a70,#3f4a4a 60%,#2e3a30)"></div>
    <div class="logo" style="left:30px;top:12px"><span class="dot"></span>VillaHaven</div>
    <div class="topbar"><span>Login</span><span>Wish List (0)</span><span class="lang">Language</span></div>
    <div class="nav"><span>Last Minute</span><span>Special Offers</span><span>Experience</span><span>Contact Us</span></div>
    <div class="hdr-title">BLOG DETAILS</div>
  </div>
  <div class="crumb">Home / Blog / <b>Blog Details</b></div>
  <div class="ph" role="img" aria-label="Hotel reception desk" style="left:29px;top:110px;width:230px;height:138px;background:linear-gradient(150deg,#8a3d32,#c98d63 45%,#e4c8a4 75%,#9a6a4a)"></div>
  <div class="abs" style="left:29px;top:258px;font-size:3px;color:#555">Jhon Doe &nbsp;|&nbsp; December 4, 2020 &nbsp;|&nbsp; 0 Comments</div>
  <div class="abs h-narrow" style="left:29px;top:268px;font-size:6px">One who avoids a pain that produces no resultant pleasure</div>
  <p class="abs" style="left:29px;top:280px;width:232px;font-size:3.2px;line-height:4.7px;color:#6a7272">Sed ut perspiciatis unde omnis iste natus error sit voluptatem accusantium doloremque laudantium, totam rem aperiam, eaque ipsa quae ab illo inventore veritatis et quasi architecto beatae vitae dicta sunt explicabo. Nemo enim ipsam voluptatem quia voluptas sit aspernatur aut odit aut fugit, sed quia consequuntur magni dolores eos qui ratione voluptatem sequi nesciunt. Neque porro quisquam est, qui dolorem ipsum quia dolor sit amet, consectetur, adipisci velit, sed quia non numquam eius modi tempora incidunt ut labore et dolore magnam aliquam quaerat voluptatem. Ut enim ad minima veniam, quis nostrum exercitationem ullam corporis suscipit laboriosam, nisi ut aliquid ex ea commodi consequatur.</p>
  <div class="abs" style="left:29px;top:334px;display:flex;gap:4px"><i style="width:4px;height:4px;border-radius:50%;background:#555;display:block"></i><i style="width:4px;height:4px;border-radius:50%;background:#555;display:block"></i><i style="width:4px;height:4px;border-radius:50%;background:#555;display:block"></i><i style="width:4px;height:4px;border-radius:50%;background:#555;display:block"></i><i style="width:4px;height:4px;border-radius:50%;background:#555;display:block"></i><i style="width:4px;height:4px;border-radius:50%;background:#555;display:block"></i></div>

  <div class="side-box" style="left:282px;top:110px;width:66px"><h6>CATEGORIES</h6><ul><li>Consectetur Adipiscing<span>›</span></li><li>Eget Tempor<span>›</span></li><li>Lobortis Dictum<span>›</span></li><li>Tempus Fermentum<span>›</span></li><li>Quisque<span>›</span></li><li>Consectetur Adipiscing<span>›</span></li><li>Eget Tempor<span>›</span></li><li>Lobortis Dictum<span>›</span></li><li>Tempus Fermentum<span>›</span></li><li>Quisque<span>›</span></li></ul></div>
  <div class="side-box" style="left:282px;top:251px;width:66px;height:28px"><h6>SEARCH</h6><div style="border:.5px solid #ccc;height:7px;font-size:2.8px;color:#999;padding:1.5px 2px;display:flex;justify-content:space-between">Search Here<span>⚲</span></div></div>
  <div class="side-box" style="left:282px;top:286px;width:66px;height:56px"><h6>POPULAR TAGS</h6><div style="display:flex;flex-wrap:wrap;gap:2px">
    <span style="font-size:2.4px;border:.4px solid #ddd;padding:1px 2px">AGENCY</span><span style="font-size:2.4px;border:.4px solid #ddd;padding:1px 2px">BUSINESS</span><span style="font-size:2.4px;border:.4px solid #ddd;padding:1px 2px">CLEAN</span><span style="font-size:2.4px;border:.4px solid #ddd;padding:1px 2px">CREATIVE</span><span style="font-size:2.4px;border:.4px solid #ddd;padding:1px 2px">DESIGN</span><span style="font-size:2.4px;border:.4px solid #ddd;padding:1px 2px">MODERN</span><span style="font-size:2.4px;border:.4px solid #ddd;padding:1px 2px">POPULAR</span></div></div>

  <div class="abs h-narrow" style="left:29px;top:369px;font-size:5.6px">LEAVE COMMENT</div>
  <div class="field" style="left:29px;top:380px;width:63px;height:9px">Your Name</div>
  <div class="field" style="left:95px;top:380px;width:63px;height:9px">Email</div>
  <div class="abs" style="left:29px;top:401px;font-size:2.8px;color:#666">▫ Save my name, email, and website in this browser for the next time I comment.</div>
  <div class="field" style="left:29px;top:410px;width:63px;height:9px">Phone</div>
  <div class="field" style="left:95px;top:410px;width:63px;height:9px">Website</div>
  <div class="field" style="left:29px;top:423px;width:129px;height:30px;align-items:flex-start">Comments</div>
  <div class="abs btn" style="left:29px;top:463px">Post Comments</div>

  <footer class="ftr" style="top:493px">
    <div class="logo" style="left:30px;top:31px"><span class="dot"></span>VillaHaven</div>
    <div class="f-sub">Subscribe to our Newsletter</div>
    <svg class="f-arrow" viewBox="0 0 24 8"><use href="#i-arrow"/></svg>
    <p class="f-desc">Our range of services is very large, and we are constantly expanding it.</p>
    <div class="f-col" style="left:162px"><h4>Navigation</h4><ul><li>Last Minute</li><li>Special Offers</li><li>Experience</li><li>Contact Us</li></ul></div>
    <div class="f-col" style="left:249px"><h4>Recent posts</h4><div class="post"><div class="thumb"></div><p>Which construction tool is better to choose?<small>2 November, 2020</small></p></div><div class="post"><div class="thumb"></div><p>Which construction tool is better to choose?<small>2 November, 2020</small></p></div></div>
    <div class="f-contact"><div class="ci"><svg><use href="#i-phone"/></svg><div><b>Call us</b>+1 555 010 2040 (USA)</div></div><div class="ci"><svg><use href="#i-mail"/></svg><div><b>Write to us</b>sales@example.com</div></div><div class="ci"><svg><use href="#i-pin"/></svg><div><b>Office location</b>12 Olive Grove Rd, Lakeside</div></div></div>
    <div class="f-legal">Privacy Policies &nbsp;/&nbsp; Reservation Policies &nbsp;/&nbsp; Cookie Policy<br>Copyright © 2021 VillaHaven. All Rights Reserved. <span>Powered by VillaHaven</span></div>
    <div class="f-social"><i></i><u></u></div>
  </footer>
</section>

</body>
</html>
```